Screening Mammography flyer for patients

We need a flyer design to inform our patients of our Screening Mammography program (it's a screening Diagnostic Imaging test). Women aged 50-74 years old are eligible for this exam. We also have a convenient booking system, when a patient can call us directly. There's no doctor’s referral needed to sign up for the test.
We are also starting the RKC Wellness Courier program, when select patients will help spread the word and save lives.
The flyer has to be done with a lot of pink color as it is a traditional color for Breast cancer materials, with consideration of the hospital's corporate colors (the brand book is attached).

Diagnostic Imaging

```html
<!DOCTYPE html>
<html lang="en">
<head>
<meta charset="utf-8">
<title>Screening Mammography Flyer</title>
<link rel="stylesheet" href="https://fonts.googleapis.com/css2?family=Lato:wght@400;700;900&family=Exo+2:wght@600&display=swap">
<style>
  :root {
    --pink-deep: #d11d6a;
    --pink-bright: #f0307f;
    --pink-soft: #f7b8d2;
    --ink: #2a2a2a;
    --brand-green: #6fb43f;
    --page-bg: #ececec;
    --paper: #ffffff;
  }
  * { margin: 0; padding: 0; box-sizing: border-box; }
  html, body { width: 1200px; height: 1075px; overflow: hidden; }
  body { background: var(--page-bg); font-family: "Lato", sans-serif; color: var(--ink); position: relative; }

  .flyer {
    position: absolute; left: 0; top: 149px;
    width: 1200px; height: 777px;
    background: var(--paper); overflow: hidden;
  }
  .flyer-shapes { position: absolute; inset: 0; width: 100%; height: 100%; }

  .headline {
    position: absolute; right: 62px; top: 40px;
    font-weight: 900; font-size: 70px; letter-spacing: -1px;
    color: var(--pink-deep); line-height: 1;
  }
  .audience {
    position: absolute; right: 62px; top: 113px;
    font-size: 50px; font-weight: 400; line-height: 1;
  }
  .referral-note {
    position: absolute; left: 585px; top: 225px; width: 360px;
    text-align: center; color: #fff; font-weight: 700; font-size: 23px; line-height: 36px;
  }
  .badge-text {
    position: absolute; left: 1036px; top: 222px; width: 86px;
    color: var(--pink-deep); font-weight: 900; text-align: right; line-height: 0.92;
  }
  .badge-text .big { display: block; font-size: 20px; }
  .badge-text .small { display: block; font-size: 9.5px; letter-spacing: 0.2px; }
  .booking {
    position: absolute; right: 62px; top: 357px;
    font-size: 23px; font-weight: 700; white-space: nowrap;
  }
  .booking .lead { color: var(--pink-deep); font-size: 31px; }
  .same-day {
    position: absolute; left: 312px; right: 0; top: 425px; height: 68px;
    display: flex; align-items: center; justify-content: center;
    font-family: "Exo 2", sans-serif; font-weight: 600; font-size: 40px; color: #fff;
  }
  .clinic-name {
    position: absolute; left: 358px; top: 544px;
    display: flex; align-items: center; gap: 14px;
    color: var(--brand-green); font-weight: 700; font-size: 17px; line-height: 1.15; letter-spacing: 1px;
  }
  .clinic-name .mark { width: 44px; height: 44px; background: var(--brand-green); flex: none; }
  .clinic-network {
    position: absolute; left: 358px; top: 610px;
    color: var(--brand-green); font-weight: 700; font-size: 11px; letter-spacing: 1.2px;
  }
  .contact-list { position: absolute; left: 640px; top: 530px; list-style: none; font-size: 19px; line-height: 1.3; }
  .contact-list li { display: flex; gap: 10px; margin-bottom: 10px; }
  .contact-list svg { flex: none; width: 16px; height: 16px; margin-top: 4px; }
  .date-line { position: absolute; left: 362px; top: 660px; font-size: 30px; white-space: nowrap; }
</style>
</head>
<body>
<main class="flyer">
  <svg class="flyer-shapes" viewBox="0 0 1374 890">
    <defs>
      <linearGradient id="photoTone" x1="0" y1="0" x2="1" y2="1">
        <stop offset="0" stop-color="#f3ede4"/>
        <stop offset="0.55" stop-color="#c9c3bc"/>
        <stop offset="1" stop-color="#f1ece6"/>
      </linearGradient>
      <radialGradient id="ribbonTone" cx="0.5" cy="0.5" r="0.5">
        <stop offset="0" stop-color="#f29cc0"/>
        <stop offset="1" stop-color="#fbe0ec"/>
      </radialGradient>
    </defs>
    <path role="img" aria-label="Photo of two smiling women in grey staff t-shirts"
          d="M0 0 H650 C540 170 450 420 385 540 C320 650 230 700 140 700 L0 690 Z" fill="url(#photoTone)"/>
    <path d="M672 0 C560 170 470 420 402 535 C330 650 235 700 140 705 C60 708 18 650 28 585 C40 505 110 470 162 480"
          fill="none" stroke="var(--pink-bright)" stroke-width="30" stroke-linecap="round"/>
    <rect x="357" y="487" width="1017" height="78" fill="var(--pink-deep)"/>
    <rect x="612" y="233" width="600" height="134" rx="67" fill="var(--pink-bright)"/>
    <circle cx="1227" cy="298" r="96" fill="#fff" stroke="var(--pink-bright)" stroke-width="10"/>
    <ellipse role="img" aria-label="Pink awareness ribbon" cx="1200" cy="310" rx="38" ry="56"
             transform="rotate(-25 1200 310)" fill="url(#ribbonTone)"/>
    <path d="M0 760 Q687 905 1374 760" fill="none" stroke="var(--pink-bright)" stroke-width="8"/>
    <path d="M0 772 Q687 918 1374 772 V890 H0 Z" fill="var(--pink-deep)"/>
  </svg>

  <h1 class="headline">JUST BOOK IT</h1>
  <p class="audience">For women aged 50-74</p>
  <p class="referral-note">No doctor's referral needed for your screening Mammogram</p>
  <p class="badge-text"><span class="big">EARLY</span><span class="small">DETECTION</span><span class="big">SAVES</span><span class="big">LIVES</span></p>
  <p class="booking"><span class="lead">To book an appointment,</span> call 555-014-2270 ext. 1180</p>
  <p class="same-day">Same Day appointments available!</p>

  <div class="clinic-name"><span class="mark"></span><span>ROSEWOOD<br>KELLER<br>CLINIC</span></div>
  <p class="clinic-network">EASTVALE HEALTH NETWORK</p>

  <ul class="contact-list">
    <li><svg viewBox="0 0 16 16"><path d="M8 1a5 5 0 0 0-5 5c0 4 5 9 5 9s5-5 5-9a5 5 0 0 0-5-5z" fill="none" stroke="var(--pink-deep)" stroke-width="1.6"/><circle cx="8" cy="6" r="1.8" fill="var(--pink-deep)"/></svg><span>Diagnostic Imaging Department at Rosewood Keller<br>Clinic, 410 Harlow Ave, Eastvale</span></li>
    <li><svg viewBox="0 0 16 16"><circle cx="8" cy="8" r="7" fill="var(--pink-deep)"/><path d="M4 6h8v5H4z M4 6l4 3 4-3" fill="none" stroke="#fff" stroke-width="1"/></svg><span>imaging@evhn.example</span></li>
    <li><svg viewBox="0 0 16 16"><circle cx="8" cy="8" r="7" fill="var(--pink-deep)"/><path d="M1 8h14M8 1c-3 3-3 11 0 14M8 1c3 3 3 11 0 14" fill="none" stroke="#fff" stroke-width="1"/></svg><span>www.evhn.example/imaging</span></li>
  </ul>

  <p class="date-line">Date and Time: _________________________</p>
</main>
</body>
</html>
```